kolvarin.link kolvarin.space kolvarin.press website

The website is named KOLVARIN and it will have 3 domain names. kolvarin.link, press, space.
I'd like it to be viewed on Pads, pcs and phones.

page menu:

kolvarin.link(start page): presentation of company. (creative, design, app, new product innovation.)
Here we'll need sosial media icons: plimber, vendoloop, mirtavel, trelvanet. (light but some 'fruity' colors)

kolvarin.press: blog. It will be a 75% picture blog > rest will be text. I need to be able to resize pictures and shape columns to picture size. (light but some 'fruity' colors)

kolvarin.space : the fun part of this web design, however, on entering the page I'd like a non-disclosure agreement where viewer simply click "yes, I agree" after filling out contact info. (check attached document)
We will have space here for uploading PDF files viewers can download. There is also a blog space here to tell in brief about the PDF file. (maybe a space/sci-fi theme her e.g spacechimp, Laika the space dog?)

I will attach the logo here I want you to use > and develop for the .space .press webpage. The logo i uploaded is for the .link page.

Target Market(s)

venture capitalists

Number of Pages Required

3 page

Requirements
Must have
• a few 'fruity colors' but mostly white and grey

```html
<!DOCTYPE html>
<html lang="en">
<head>
<meta charset="utf-8">
<title>Kolvarin — Creative Design &amp; Application</title>
<link rel="stylesheet" href="https://fonts.googleapis.com/css2?family=Lato:wght@400;700;900&family=Signika:wght@500;600&family=Cabin:wght@400&display=swap">
<style>
  :root {
    --page-bg: #f3f3f3;
    --band-bg: #ececec;
    --ink: #1d1d1d;
    --ink-soft: #333333;
    --accent-red: #e34b2f;
    --nav-blue: #0b5fae;
    --nav-blue-dark: #08457f;
    --nav-rule: #e8442c;
    --fruit-green: #6fb523;
    --orange-a: #ffae00;
    --orange-b: #ff7a00;
    --green-a: #c3d300;
    --green-b: #4f9e1c;
    --blue-a: #0a7be0;
    --blue-b: #0a4f9c;
    --red-a: #ff6e5a;
    --red-b: #f24c36;
    --footer-bg: #000000;
  }
  * { margin: 0; padding: 0; box-sizing: border-box; }
  html, body { width: 1200px; height: 997px; overflow: hidden; }
  body {
    position: relative;
    background: var(--page-bg);
    font-family: "Lato", sans-serif;
    color: var(--ink);
  }

  /* Header */
  .brand {
    position: absolute; left: 80px; top: 40px;
    display: flex; align-items: center; gap: 10px;
    font-family: "Lato", sans-serif; font-weight: 900;
    font-size: 30px; color: var(--ink); letter-spacing: 1px;
  }
  .brand-square { width: 22px; height: 22px; background: var(--orange-a); }
  .contact { position: absolute; top: 44px; display: flex; align-items: center; gap: 8px; }
  .contact-call { left: 688px; }
  .contact-mail { left: 918px; }
  .contact-label { font-weight: 700; font-size: 17px; color: var(--ink-soft); line-height: 22px; }
  .contact-value { font-size: 17px; color: var(--ink-soft); line-height: 22px; }

  /* Navigation */
  .main-nav {
    position: absolute; left: 0; top: 129px; width: 1200px; height: 49px;
    background: linear-gradient(var(--nav-blue), #0a559d);
    border-bottom: 3px solid var(--nav-rule);
    height: 52px;
  }
  .nav-list { position: absolute; left: 82px; top: 0; display: flex; list-style: none; height: 49px; }
  .nav-item {
    font-family: "Cabin", sans-serif; font-size: 19px; color: #fff;
    display: flex; align-items: center; justify-content: center;
    border-right: 1px solid rgba(0,0,0,.18);
    border-left: 1px solid rgba(255,255,255,.08);
    position: relative;
  }
  .nav-item.is-active { background: var(--nav-blue-dark); }
  .nav-item.is-active::after {
    content: ""; position: absolute; bottom: -3px; left: 50%; margin-left: -6px;
    border: 6px solid transparent; border-bottom-color: var(--nav-rule); border-top: 0;
  }
  .nav-social { position: absolute; left: 945px; top: 6px; display: flex; gap: 9px; }
  .nav-social span {
    width: 37px; height: 37px; border-radius: 50%;
    border: 2px solid rgba(0,0,0,.25); background: rgba(255,255,255,.06);
    color: #fff; font-size: 7.5px; display: flex; align-items: center; justify-content: center;
  }

  /* Hero */
  .hero-title {
    position: absolute; left: 80px; top: 296px;
    font-family: "Signika", sans-serif; font-weight: 600; font-size: 34px; line-height: 44px;
    color: var(--ink);
  }
  .hero-title .muted { color: #3a3a3a; }
  .hero-title .accent { color: var(--accent-red); }
  .hero-art {
    position: absolute; left: 430px; top: 235px; width: 680px; height: 350px;
    background: radial-gradient(ellipse at 50% 60%, rgba(255,210,60,.35), rgba(160,100,200,.18) 45%, rgba(243,243,243,0) 72%);
  }

  /* Lower band */
  .lower-band { position: absolute; left: 0; top: 658px; width: 1200px; height: 274px; background: var(--band-bg); }

  /* Features */
  .features { position: absolute; left: 80px; top: 590px; width: 1040px; height: 128px; }
  .features svg.strip { position: absolute; left: 0; top: 0; }
  .feature { position: absolute; top: 22px; color: #1e1e1e; }
  .feature-head { display: flex; align-items: center; gap: 8px; }
  .feature-title { font-weight: 700; font-size: 21px; color: #2a2a2a; text-shadow: 0 1px 0 rgba(255,255,255,.35); }
  .feature-text { margin-top: 14px; font-size: 14.5px; line-height: 20px; }
  .feature-app .feature-text { color: #0c3f79; }

  /* About */
  .about-title {
    position: absolute; left: 0; top: 760px; width: 1200px; text-align: center;
    font-weight: 700; font-size: 33px; color: var(--ink-soft);
  }
  .about-title .accent { color: var(--fruit-green); }
  .about-text {
    position: absolute; left: 110px; top: 816px; width: 980px; text-align: center;
    font-size: 14.6px; line-height: 25.5px; color: #333;
  }

  /* Footer */
  .site-footer { position: absolute; left: 0; top: 932px; width: 1200px; height: 65px; background: var(--footer-bg); }
  .copyright { position: absolute; left: 84px; top: 24px; color: #fff; font-weight: 700; font-size: 13.5px; }
  .footer-social { position: absolute; left: 917px; top: 12px; display: flex; gap: 12px; }
  .footer-social span {
    width: 42px; height: 42px; border-radius: 50%;
    color: #fff; font-size: 8.5px; font-weight: 700;
    display: flex; align-items: center; justify-content: center;
  }
  .social-a { background: #f2b600; }
  .social-b { background: #f07010; }
  .social-c { background: #5cb81d; }
  .social-d { background: #6a2be0; }
</style>
</head>
<body>

<header class="site-header">
  <div class="brand"><span class="brand-square"></span>KOLVARIN</div>

  <div class="contact contact-call">
    <svg width="40" height="46" viewBox="0 0 40 46" aria-hidden="true">
      <path d="M22 4 A19 19 0 1 0 22 42" fill="none" stroke="#e34b2f" stroke-width="2.5"/>
      <path d="M13 13 l5 -2 l3 7 l-3 2 q2 6 6 9 l3 -2 l5 5 l-3 4 q-10 -2 -16 -14 z" fill="#e34b2f"/>
    </svg>
    <div><div class="contact-label">Call Us:</div><div class="contact-value">+1 555 0143 862</div></div>
  </div>

  <div class="contact contact-mail">
    <svg width="46" height="46" viewBox="0 0 46 46" aria-hidden="true">
      <path d="M3 16 L38 4 L44 34 L9 44 Z" fill="#fff" stroke="#e34b2f" stroke-width="3" stroke-linejoin="round"/>
      <path d="M3 16 L26 28 L38 4" fill="none" stroke="#e34b2f" stroke-width="3" stroke-linejoin="round"/>
    </svg>
    <div><div class="contact-label">Mail Us:</div><div class="contact-value">hello@kolvarin.link</div></div>
  </div>
</header>

<nav class="main-nav">
  <ul class="nav-list">
    <li class="nav-item is-active" style="width:118px">HOME</li>
    <li class="nav-item" style="width:128px">ABOUT</li>
    <li class="nav-item" style="width:146px">SPACE</li>
    <li class="nav-item" style="width:118px">PRESS</li>
  </ul>
  <div class="nav-social">
    <span>mirtavel</span><span>plimber</span><span>vendoloop</span><span>trelvanet</span>
  </div>
</nav>

<section class="hero">
  <h1 class="hero-title">
    We Made <span class="muted">Creative Design</span><br>
    &amp; Application For<br>
    <span class="accent">New Product Innovation</span>
  </h1>
  <div class="hero-art" role="img" aria-label="Illustration of crumpled paper balls in red, green, purple, yellow light bulb and peach, with colourful sketched arrows"></div>
</section>

<div class="lower-band"></div>

<section class="features">
  <svg class="strip" width="1040" height="128" viewBox="0 0 1040 128" aria-hidden="true">
    <defs>
      <linearGradient id="g-orange" x1="0" y1="0" x2="0" y2="1"><stop offset="0" stop-color="#ffae00"/><stop offset="1" stop-color="#ff7a00"/></linearGradient>
      <linearGradient id="g-green" x1="0" y1="0" x2="0" y2="1"><stop offset="0" stop-color="#c3d300"/><stop offset="1" stop-color="#4f9e1c"/></linearGradient>
      <linearGradient id="g-blue" x1="0" y1="0" x2="0" y2="1"><stop offset="0" stop-color="#0a7be0"/><stop offset="1" stop-color="#0a4f9c"/></linearGradient>
      <linearGradient id="g-red" x1="0" y1="0" x2="0" y2="1"><stop offset="0" stop-color="#ff6e5a"/><stop offset="1" stop-color="#f24c36"/></linearGradient>
    </defs>
    <path d="M827 0 H1034 a6 6 0 0 1 6 6 V122 a6 6 0 0 1 -6 6 H747 L781 64 L747 0 Z" fill="url(#g-red)"/>
    <path d="M500 0 H781 L815 64 L781 128 H500 Z" fill="url(#g-blue)"/>
    <path d="M253 0 H535 L569 64 L535 128 H253 Z" fill="url(#g-green)"/>
    <path d="M6 0 H287 L321 64 L287 128 H6 a6 6 0 0 1 -6 -6 V6 a6 6 0 0 1 6 -6 Z" fill="url(#g-orange)"/>
  </svg>

  <div class="feature" style="left:24px">
    <div class="feature-head">
      <svg width="38" height="32" viewBox="0 0 38 32" aria-hidden="true"><rect x="2" y="4" width="32" height="20" fill="none" stroke="#222" stroke-width="2.5"/><path d="M12 30 H26 M19 24 V30 M14 18 L28 4" stroke="#222" stroke-width="2.5"/></svg>
      <span class="feature-title">Creative</span>
    </div>
    <p class="feature-text">Lorem ipsum dolor sit amet,<br>consectetur adipiscing elit,</p>
  </div>

  <div class="feature" style="left:314px">
    <div class="feature-head">
      <svg width="36" height="36" viewBox="0 0 36 36" aria-hidden="true"><path d="M4 8 L8 4 L32 28 L32 32 L28 32 Z" fill="none" stroke="#222" stroke-width="2.2"/><path d="M28 4 L32 8 L8 32 L4 28 Z" fill="none" stroke="#222" stroke-width="2.2"/></svg>
      <span class="feature-title">Design</span>
    </div>
    <p class="feature-text">Lorem ipsum dolor sit amet,<br>consectetur adipiscing elit,</p>
  </div>

  <div class="feature feature-app" style="left:558px">
    <div class="feature-head">
      <svg width="32" height="38" viewBox="0 0 32 38" aria-hidden="true"><rect x="2" y="2" width="18" height="34" rx="3" fill="none" stroke="#1a1a1a" stroke-width="2.5"/><circle cx="20" cy="20" r="6" fill="#1a1a1a"/><circle cx="20" cy="20" r="2.5" fill="#0a68c4"/></svg>
      <span class="feature-title">App</span>
    </div>
    <p class="feature-text">Lorem ipsum dolor sit amet,<br>consectetur adipiscing elit,</p>
  </div>

  <div class="feature" style="left:796px">
    <div class="feature-head">
      <svg width="44" height="44" viewBox="0 0 44 44" aria-hidden="true"><path d="M16 28 a9 9 0 1 1 12 0 v6 h-12 z" fill="none" stroke="#222" stroke-width="2.2"/><path d="M17 38 H27 M19 41 H25 M22 2 V7 M8 8 L11 11 M36 8 L33 11 M2 20 H7 M37 20 H42" stroke="#222" stroke-width="2"/></svg>
      <span class="feature-title">Product Innovation</span>
    </div>
    <p class="feature-text">Lorem ipsum dolor sit amet,<br>consectetur adipiscing elit,</p>
  </div>
</section>

<section class="about">
  <h2 class="about-title">About <span class="accent">Kolvarin</span></h2>
  <p class="about-text">Lorem ipsum dolor sit amet, consectetur adipiscing elit, sed do eiusmod tempor incididunt ut labore et dolore magna aliqua. Ut enim ad minim veniam, quis nostrud exercitation ullamco laboris nisi ut aliquip ex ea commodo consequat. Duis aute irure dolor in reprehenderit in voluptate velit esse cillum dolore eu fugiat nulla pariatur. Excepteur sint occaecat cupidatat non proident, sunt in culpa qui officia deserunt mollit anim id est laborum.</p>
</section>

<footer class="site-footer">
  <p class="copyright">Copyright &nbsp;©2016 &nbsp;Kolvarin. All rights reserved.</p>
  <div class="footer-social">
    <span class="social-a">mirtavel</span>
    <span class="social-b">plimber</span>
    <span class="social-c">trelvanet</span>
    <span class="social-d">vendoloop</span>
  </div>
</footer>

</body>
</html>
```